Telecommunications/Power civil contractor needs business card design

Were a new telecommunications/power underground civil contractor that is looking for a new business card design. Our company colours are silver or grey and orange. Feel free to use the white background logo or the black background logo.

Target Market(s)

Local contractors, utility companies, private sector mining/energy companies, developers.

Industry/Entity Type

Telecommunications

Contact Information for Business Card

Each card will need the following info:
Persons name:
Title:
E-mail:
Phone number:
Shop Address:
Mailing Address:

Requirements
Must have
• Each card will need the following info:
• Persons name:
• Title:
• E-mail:
• Phone number:
• Shop Address:
• Mailing Address:

```html
<!DOCTYPE html>
<html lang="en">
<head>
<meta charset="utf-8">
<title>Trenchline Contracting – Business Card</title>
<link href="https://fonts.googleapis.com/css2?family=Montserrat:wght@300;400;500;800&display=swap" rel="stylesheet">
<style>
  :root {
    --backdrop: #e9e7e3;
    --card-white: #fbfbfb;
    --steel: #6e6f71;
    --steel-dark: #5a5b5d;
    --steel-light: #b9babc;
    --orange: #ea6a2c;
    --ink: #595a5c;
    --text-soft: #7b7c7e;
    --on-steel: #ffffff;
  }
  html, body {
    margin: 0;
    width: 1200px;
    height: 1022px;
    overflow: hidden;
    background: var(--backdrop);
    font-family: "Montserrat", sans-serif;
  }
  .card {
    position: absolute;
    left: 150px;
    top: 254px;
    width: 900px;
    height: 514px;
    border-radius: 22px;
    overflow: hidden;
    background: var(--card-white);
    box-shadow: 0 6px 24px rgba(0,0,0,0.18);
  }
  .card-art {
    position: absolute;
    inset: 0;
  }
  .identity {
    position: absolute;
    left: 60px;
    top: 100px;
    color: var(--ink);
  }
  .wordmark {
    margin: 0;
    font-weight: 800;
    color: var(--steel-dark);
    line-height: 1;
    letter-spacing: 0.5px;
  }
  .wordmark-main { display: block; font-size: 44px; }
  .wordmark-sub  { display: block; font-size: 21px; margin-top: 6px; letter-spacing: 1px; }
  .person-name {
    margin: 26px 0 0;
    font-weight: 500;
    font-size: 30px;
    color: var(--orange);
    letter-spacing: 0.5px;
  }
  .person-title {
    margin: 2px 0 0;
    font-weight: 400;
    font-size: 19px;
    color: var(--text-soft);
  }
  .address {
    margin: 24px 0 0;
    font-style: normal;
    font-weight: 300;
    font-size: 21px;
    line-height: 1.3;
    color: var(--text-soft);
  }
  .address + .address { margin-top: 14px; }
  .contact {
    position: absolute;
    right: 38px;
    top: 292px;
    margin: 0;
    padding: 0;
    list-style: none;
    color: var(--on-steel);
    font-weight: 400;
    font-size: 17px;
    line-height: 1.5;
  }
  .contact li { display: flex; align-items: center; gap: 10px; white-space: nowrap; }
  .contact svg { width: 15px; height: 15px; flex: none; }
</style>
</head>
<body>
<div class="card">
  <svg class="card-art" viewBox="0 0 900 514" aria-hidden="true">
    <defs>
      <linearGradient id="steelFill" x1="0" y1="0" x2="1" y2="1">
        <stop offset="0" stop-color="#7a7b7d"/>
        <stop offset="1" stop-color="#5c5d5f"/>
      </linearGradient>
    </defs>
    <path d="M560 0 H900 V514 H330 C430 440 505 360 505 255 C505 180 560 100 560 0 Z" fill="url(#steelFill)"/>
    <path d="M505 255 C505 360 430 440 330 514 H300 C410 440 482 360 482 255 Z" fill="var(--steel-light)"/>
    <path d="M488 255 C488 360 415 440 312 514" fill="none" stroke="var(--orange)" stroke-width="6"/>
    <rect x="506" y="0" width="26" height="60" fill="var(--orange)"/>
    <circle cx="520" cy="150" r="100" fill="var(--card-white)" stroke="var(--steel-light)" stroke-width="12"/>
    <path d="M0 390 C60 450 120 490 240 514 H0 Z" fill="var(--steel-light)"/>
    <path d="M0 432 C50 478 100 502 170 514 H0 Z" fill="var(--orange)"/>
  </svg>

  <div class="identity">
    <h1 class="wordmark">
      <span class="wordmark-main">TRENCHLINE</span>
      <span class="wordmark-sub">CONTRACTING INC</span>
    </h1>
    <p class="person-name">MARCUS HALDEN</p>
    <p class="person-title">Director</p>
    <address class="address">48 Quarry Lane<br>Millbrook, NY 12545</address>
    <address class="address">PO BOX 3318<br>LAKESIDE, CA 92040</address>
  </div>

  <ul class="contact">
    <li>
      <svg viewBox="0 0 16 16"><rect x="4" y="1" width="8" height="14" rx="1.5" fill="none" stroke="var(--orange)" stroke-width="1.6"/></svg>
      +330 5550-1842
    </li>
    <li>
      <svg viewBox="0 0 16 16"><path d="M3 2 L6 2 L7 5 L5 6.5 C6 9 7 10 9.5 11 L11 9 L14 10 L14 13 C8 14 2 8 3 2 Z" fill="var(--orange)"/></svg>
      +330 5550-2963
    </li>
    <li>
      <svg viewBox="0 0 16 16"><rect x="1.5" y="3.5" width="13" height="9" fill="none" stroke="var(--orange)" stroke-width="1.6"/><path d="M1.5 3.5 L8 9 L14.5 3.5" fill="none" stroke="var(--orange)" stroke-width="1.4"/></svg>
      info@trenchlinecontracting.com
    </li>
    <li>
      <svg viewBox="0 0 16 16"><circle cx="8" cy="8" r="6.5" fill="none" stroke="var(--orange)" stroke-width="1.5"/><path d="M1.5 8 H14.5 M8 1.5 C5 5 5 11 8 14.5 C11 11 11 5 8 1.5" fill="none" stroke="var(--orange)" stroke-width="1.2"/></svg>
      www.trenchlinecontracting.com
    </li>
  </ul>
</div>
</body>
</html>
```